Jolly Paws Business Card Update

I have a business card which I love. I want to keep the same logo, colours, font and style. I want to upgrade the scripting and remove some elements and add others.
On the front side under Services - remove the existing wording and insert - Providing individual coaching strategies to create happy, healthy and social canine companions
Under Denise Carvell amend the current wording to read: Qualified in Dog Behavioural Training, Natural Animal Healthcare and Animal Health Science
On the reverse side to remove the web address.

```html
<!DOCTYPE html>
<html lang="en">
<head>
<meta charset="utf-8">
<title>Jolly Paws Business Card</title>
<link href="https://fonts.googleapis.com/css2?family=Arimo:wght@400;700&family=Open+Sans:ital,wght@0,400;0,600;1,400&display=swap" rel="stylesheet">
<style>
  :root {
    --page: #2a2a2b;
    --blue-deep: #1f3f8f;
    --blue-mid: #1b5fae;
    --blue-light: #0a8fd0;
    --navy: #26357f;
    --red-deep: #7a1a1d;
    --red: #c41e24;
    --cream: #ece4cc;
    --card-white: #efefef;
    --text-light: #f2f2f2;
  }
  * { margin: 0; padding: 0; box-sizing: border-box; }
  html, body { width: 1200px; height: 1138px; overflow: hidden; background: var(--page); }
  .card {
    position: absolute; left: 276px; width: 620px; height: 374px;
    border-radius: 14px; overflow: hidden;
    box-shadow: 0 4px 10px rgba(0,0,0,.45);
  }
  /* Front */
  .card-front {
    top: 186px;
    background: linear-gradient(200deg, var(--blue-light) 0%, var(--blue-mid) 45%, var(--blue-deep) 100%);
  }
  .brand-name {
    position: absolute; left: 34px; top: 50px;
    font: 600 34px/1 "Open Sans", sans-serif; letter-spacing: 1px;
    color: var(--text-light); text-transform: uppercase;
  }
  .brand-tagline {
    position: absolute; left: 34px; top: 90px;
    font: 400 16.5px/1 "Open Sans", sans-serif; color: var(--text-light);
  }
  .services-front {
    position: absolute; left: 38px; top: 184px; width: 230px;
    font: 400 15.5px/1.22 "Arimo", sans-serif; color: var(--text-light);
  }
  .services-front h3 { font: 700 15.5px/1.22 "Arimo", sans-serif; }
  .emblem {
    position: absolute; border-radius: 50%;
    background: radial-gradient(circle, #fbf7ea 0%, var(--cream) 75%);
    border: 22px solid var(--red);
    display: flex; align-items: center; justify-content: center;
    color: var(--navy); font-family: "Open Sans", sans-serif; font-weight: 600;
  }
  .emblem-front { left: 602px; top: 38px; width: 260px; height: 260px; font-size: 28px; }
  .front-band {
    position: absolute; left: 0; bottom: 0; width: 100%; height: 52px;
    background: linear-gradient(90deg, var(--red-deep), var(--red) 50%, var(--red-deep));
    display: flex; align-items: center; justify-content: center;
    font: 400 16px/1 "Arimo", sans-serif; color: var(--text-light);
  }
  /* Back */
  .card-back { top: 608px; background: var(--card-white); }
  .person-name {
    position: absolute; left: 41px; top: 46px;
    font: 600 23px/1 "Open Sans", sans-serif; color: var(--navy);
  }
  .qualifications {
    position: absolute; left: 41px; top: 78px;
    font: italic 400 15.5px/1.35 "Open Sans", sans-serif; color: var(--navy);
  }
  .contacts { position: absolute; left: 41px; top: 170px; list-style: none; }
  .contacts li {
    display: flex; align-items: center; gap: 12px; height: 23px;
    font: 400 16px/1 "Open Sans", sans-serif; color: var(--navy);
  }
  .contacts svg { width: 14px; height: 14px; fill: var(--red); }
  .emblem-back { left: 439px; top: 40px; width: 134px; height: 134px; border-width: 12px; font-size: 16px; }
  .back-wave { position: absolute; left: 0; top: 0; width: 620px; height: 374px; }
  .services-back {
    position: absolute; right: 25px; top: 274px; text-align: right;
    font: 400 16px/1.2 "Arimo", sans-serif; color: var(--text-light);
  }
  .services-back h3 { font: 700 16px/1.2 "Arimo", sans-serif; }
</style>
</head>
<body>
  <section class="card card-front">
    <div class="brand-name">Jolly Paws</div>
    <div class="brand-tagline">HAPPY DOGS, HAPPY OWNERS</div>
    <div class="services-front">
      <h3>SERVICES</h3>
      <p>Providing individual coaching strategies to create happy, healthy and social canine companions</p>
    </div>
    <div class="emblem emblem-front" style="left:329px">Jolly Paws</div>
    <div class="front-band">Promoting communication and connection between dogs and their families</div>
  </section>

  <section class="card card-back">
    <svg class="back-wave" viewBox="0 0 620 374" aria-hidden="true">
      <defs>
        <linearGradient id="redFill" x1="0" x2="1" y1="0" y2="0">
          <stop offset="0" stop-color="#7a1a1d"/>
          <stop offset="0.5" stop-color="#c41e24"/>
          <stop offset="1" stop-color="#7a1a1d"/>
        </linearGradient>
      </defs>
      <path d="M0 290 C120 340 230 330 330 290 C430 250 520 205 620 225 L620 374 L0 374 Z" fill="url(#redFill)"/>
      <path d="M0 250 C110 315 230 330 330 285 C430 240 520 190 620 210 L620 222 C520 205 430 255 330 297 C230 338 110 325 0 268 Z" fill="#1c4fa6"/>
      <path d="M50 270 C150 320 230 320 300 300 C230 330 140 320 50 270 Z" fill="#2a62b5"/>
    </svg>
    <div class="person-name">Denise Carvell</div>
    <div class="qualifications">Qualified in Dog Behavioural Training,<br>Natural Animal Healthcare and<br>Animal Health Science</div>
    <ul class="contacts">
      <li><svg viewBox="0 0 14 14"><rect x="3" y="0" width="8" height="14" rx="1.5"/><rect x="4.5" y="2" width="5" height="5" fill="#efefef"/></svg>0412 555 708</li>
      <li><svg viewBox="0 0 14 14"><rect x="0" y="3" width="14" height="9"/><path d="M0 3 L7 8 L14 3" stroke="#efefef" stroke-width="1.2" fill="none"/></svg>jollypaws1@mailbox.net</li>
    </ul>
    <div class="emblem emblem-back">Jolly Paws</div>
    <div class="services-back">
      <h3>SERVICES:</h3>
      <p>Providing Individual Coaching<br>Strategies to Create Happy,<br>Healthy &amp; Social Canine Companions</p>
    </div>
  </section>
</body>
</html>
```